Exciting new website for concierge aesthetic company

Simple, elegant, fresh design for female owned concierge aesthetic company, catering to both men and women ages 30-60. We would like a home page with an exciting catch phrase, a brief description of the company and a section to fill out an appointment request that includes a section for a referral. Please also have a book appointment link in the header of all pages that will link back to booking information form on home page. Separate pages to include:
- Services = 3 different services. Each service stating the name of the service and then providing a brief description. 3 services are "Private Session" for 1 client, "Group Session" for 2-5 clients, "Party" for 6+ clients. Will provide service descriptions text later. Item at bottom of page to allow description of how to "Host a Party".
- Products = 4 different product lines. Will provide pictures of product, brief description and link to manufacturer's website.
- Stories = brief client reviews to include before and after photos
- About us = Personal picture with brief description of owner's fun, exciting and family focussed lifestyle.
*Our domain is registered with varnix and we be using varnix for website hosting.

Target Market(s)

30-60 year old men and women, but mostly women

Industry/Entity Type

beauty and aesthetics

Coding

Coded - Design and coding required

Number of Pages Required

5+ page

Font styles to use
Sans Serif
Script

Colors
59FF00
82FF00
B8FF75
E3FFCB
F4FFEA
FFC000
F8CF3A
FAE287
FDF2CF
FEFAEE
F0912C
F2A743
F7CA91
FBE8D2
FDF5EE
E54698
E96AAD
F1A4CE
F9D9EA
FCEFF6

Requirements
Must have
• coded for varnix
Should not have
• corny pictures. No needles in pictures or graphics. No medical office or medical chair in pictures.

```html
<!DOCTYPE html>
<html lang="en">
<head>
<meta charset="utf-8">
<title>Lumé Muse — Concierge Aesthetics</title>
<link href="https://fonts.googleapis.com/css2?family=Dancing+Script:wght@500;600;700&family=Raleway:wght@400;500;600&display=swap" rel="stylesheet">
<style>
:root{
  --pink:#E54698;
  --pink-mid:#E96AAD;
  --pink-soft:#F1A4CE;
  --pink-pale:#F9D9EA;
  --pink-mist:#FCEFF6;
  --orange:#F0912C;
  --orange-mid:#F2A743;
  --peach:#F7CA91;
  --peach-pale:#FBE8D2;
  --cream:#FDF5EE;
  --text:#6e6e6e;
  --dark:#3a3a3a;
  --line:#e2d6d0;
  --white:#ffffff;
}
*{box-sizing:border-box;margin:0;padding:0}
html,body{width:1200px;height:3734px;overflow:hidden}
body{position:relative;background:var(--white);font-family:"Raleway",sans-serif;color:var(--text)}
.abs{position:absolute}

/* header */
.site-header{position:absolute;left:0;top:0;width:1200px;height:107px;background:var(--white);z-index:5}
.brand{position:absolute;left:113px;top:24px;display:flex;align-items:center;gap:12px}
.brand-mark{width:58px;height:58px;border-radius:50%;border:2px solid var(--pink-mid);flex:none}
.brand-name{font-weight:600;font-size:30px;color:var(--pink);line-height:1;white-space:nowrap}
.brand-sub{font-size:9px;letter-spacing:5px;color:var(--orange);margin-top:7px;white-space:nowrap}
.main-nav{position:absolute;left:445px;top:44px;display:flex}
.main-nav a{font-size:15px;color:var(--dark);text-decoration:none;margin-right:39px}
.btn-book{position:absolute;left:907px;top:28px;width:180px;height:56px;background:var(--pink);color:var(--white);border-radius:16px 0 16px 0;display:flex;align-items:center;justify-content:center;font-family:"Dancing Script",cursive;font-size:20px;font-weight:600;text-decoration:none}

/* hero */
.hero{position:absolute;left:0;top:107px;width:1200px;height:735px;background:linear-gradient(90deg,#d8c3b3 0%,#e9d9cd 35%,#efe7e2 55%,#f3eeeb 100%);overflow:hidden}
.hero-photo{position:absolute;left:0;top:0;width:680px;height:735px;background:
  radial-gradient(ellipse 260px 330px at 470px 300px,rgba(242,214,196,.95) 0%,rgba(226,190,166,.7) 55%,transparent 100%),
  radial-gradient(ellipse 260px 420px at 140px 330px,rgba(214,178,128,.9) 0%,rgba(214,178,128,.4) 60%,transparent 100%),
  linear-gradient(90deg,#cfb193 0%,#e3cdbd 60%,rgba(239,231,226,0) 100%)}
.hero-title{position:absolute;left:640px;top:200px;width:460px;text-align:center;font-weight:600;font-size:66px;color:var(--pink);line-height:1;white-space:nowrap}
.hero-sub{position:absolute;left:655px;top:308px;width:440px;text-align:center;font-size:17px;letter-spacing:10px;color:var(--orange);white-space:nowrap}
.btn-start{position:absolute;background:var(--pink);color:var(--white);border-radius:16px 0 16px 0;display:flex;align-items:center;justify-content:center;font-family:"Dancing Script",cursive;font-size:21px;font-weight:600;text-decoration:none}
.hero .btn-start{left:803px;top:374px;width:137px;height:56px}
.dots{position:absolute;left:577px;top:616px;display:flex;gap:6px}
.dots span{width:10px;height:10px;border-radius:50%;background:#c9c2bf}
.dots span.on{background:var(--orange)}

.section-title{position:absolute;left:0;width:1200px;text-align:center;font-family:"Dancing Script",cursive;font-weight:600;font-size:42px;color:var(--pink)}

/* products */
.product-card{position:absolute;top:997px;width:229px;height:380px;background:var(--white);box-shadow:0 3px 14px rgba(0,0,0,.12);text-align:center}
.product-card .media{position:absolute;left:9px;top:9px;width:211px;height:162px}
.product-card h3{position:absolute;left:0;top:188px;width:100%;font-family:"Dancing Script",cursive;font-weight:600;font-size:21px;color:var(--dark)}
.product-card p{position:absolute;left:20px;top:229px;width:189px;font-size:12.5px;line-height:22px;color:var(--text)}
.product-card .btn-details{position:absolute;left:51px;top:306px;width:128px;height:52px;border:2px solid var(--pink);border-radius:16px 0 16px 0;display:flex;align-items:center;justify-content:center;font-family:"Dancing Script",cursive;font-size:19px;color:var(--pink);text-decoration:none}
.product-card.active{background:var(--pink)}
.product-card.active h3,.product-card.active p{color:var(--white)}
.product-card.active .btn-details{border-color:var(--white);color:var(--white)}

/* about */
.about-photo{position:absolute;left:158px;top:1608px;width:424px;height:424px;border-radius:50%;background:
  radial-gradient(ellipse 120px 150px at 52% 38%,#f3dccd 0%,#e6c2ab 60%,transparent 100%),
  radial-gradient(ellipse 200px 230px at 50% 45%,#6d4634 0%,#8c6450 55%,transparent 100%),
  linear-gradient(180deg,#f1ebe8,#efe5e1);border-bottom:5px solid var(--orange)}
.about-title{position:absolute;left:685px;top:1630px;font-family:"Dancing Script",cursive;font-weight:600;font-size:42px;color:var(--pink)}
.about-text{position:absolute;left:685px;top:1704px;width:398px;font-size:13.5px;line-height:25.8px;color:var(--text);text-align:justify}
.about .btn-start{left:685px;top:1962px;width:137px;height:55px}

/* services */
.service-box{position:absolute;top:2366px;width:228px;height:238px;border:2px solid var(--orange);background:var(--white);text-align:center}
.service-box svg{position:absolute;left:50%;transform:translateX(-50%);top:34px}
.service-box h3{position:absolute;left:0;top:140px;width:100%;font-family:"Dancing Script",cursive;font-weight:600;font-size:23px;color:var(--dark)}
.service-box p{position:absolute;left:16px;top:176px;width:196px;font-size:13px;line-height:22px;color:var(--text)}

/* appointment request */
.booking{position:absolute;left:111px;top:2628px;width:978px;height:56px;display:flex;align-items:center;gap:10px}
.booking h3{font-family:"Dancing Script",cursive;font-weight:600;font-size:25px;color:var(--pink);white-space:nowrap;margin-right:6px}
.booking .field{height:42px;border:1px solid var(--pink-soft);border-radius:10px 0 10px 0;background:var(--white);font-family:"Raleway",sans-serif;font-size:13px;color:var(--text);padding:0 12px}
.booking .field::placeholder{color:#a59a97}
.booking .btn-send{height:42px;width:112px;flex:none;border:0;background:var(--pink);color:var(--white);border-radius:14px 0 14px 0;font-family:"Dancing Script",cursive;font-size:19px;font-weight:600}

/* stories */
.story{position:absolute;top:2968px;width:472px;height:256px;border-radius:14px;overflow:hidden;box-shadow:0 3px 12px rgba(0,0,0,.08)}
.story .split{position:absolute;left:50%;top:0;width:2px;height:100%;background:rgba(255,255,255,.9)}

/* footer */
.footer-brand{position:absolute;left:103px;top:3414px;width:280px;text-align:center}
.footer-brand .brand-mark{width:96px;height:96px;margin:0 auto 16px;border-width:3px}
.footer-brand .brand-name{font-size:42px}
.footer-brand .brand-sub{font-size:10px;letter-spacing:6px;margin-top:10px}
.footer-col{position:absolute;top:3440px}
.footer-col h4{font-family:"Dancing Script",cursive;font-weight:600;font-size:26px;color:var(--dark);margin-bottom:18px}
.footer-col a{display:block;font-size:15px;color:var(--dark);text-decoration:none;line-height:26px}
.footer-rule{position:absolute;left:111px;top:3640px;width:978px;height:1px;background:#d8d8d8}
.copyright{position:absolute;left:111px;top:3667px;font-size:14.5px;color:var(--dark)}
.social{position:absolute;left:968px;top:3668px;display:flex;gap:20px}
.social span{width:16px;height:16px;border-radius:50%;background:var(--orange)}
</style>
</head>
<body>

<header class="site-header">
  <div class="brand">
    <span class="brand-mark"></span>
    <div>
      <div class="brand-name">Lumé Muse</div>
      <div class="brand-sub">CONCIERGE AESTHETICS</div>
    </div>
  </div>
  <nav class="main-nav">
    <a href="#">Home</a><a href="#">About</a><a href="#">Services</a><a href="#">Products</a><a href="#">Stories</a>
  </nav>
  <a class="btn-book" href="#booking">Book Appointment</a>
</header>

<section class="hero">
  <div class="hero-photo" role="img" aria-label="Portrait of a blonde woman in profile with facial contour lift lines"></div>
  <div class="hero-title">Lumé Muse</div>
  <div class="hero-sub">CONCIERGE AESTHETICS</div>
  <a class="btn-start" href="#booking">Get Started</a>
  <div class="dots"><span></span><span class="on"></span><span></span></div>
  <svg class="abs" style="left:0;top:580px" width="1200" height="160" viewBox="0 0 1200 160">
    <defs>
      <linearGradient id="waveHero" x1="0" x2="1">
        <stop offset="0" stop-color="#E54698"/><stop offset="1" stop-color="#F0912C"/>
      </linearGradient>
    </defs>
    <path d="M0 75 C 120 140, 230 155, 380 140 C 620 115, 850 10, 1000 20 C 1090 26, 1160 70, 1200 100 L1200 160 L0 160 Z" fill="#ffffff"/>
    <path d="M80 120 C 200 155, 300 150, 380 140 C 620 115, 850 10, 1000 20 C 1090 26, 1160 70, 1200 100" fill="none" stroke="url(#waveHero)" stroke-width="8"/>
  </svg>
</section>

<h2 class="section-title" style="top:912px">Our Products</h2>

<article class="product-card" style="left:111px">
  <div class="media" role="img" aria-label="Close-up of glossy lips with a gloved hand" style="background:radial-gradient(ellipse 70px 40px at 40% 55%,#d98a97,transparent),linear-gradient(135deg,#f3c4d2,#ecaab9 55%,#f4e6e4)"></div>
  <h3>Lorem ipsum dolor</h3>
  <p>Lorem ipsum dolor sit amet, consectetur adipiscing elit, sed aliqua.</p>
  <a class="btn-details" href="#">View Details</a>
</article>
<article class="product-card active" style="left:360px">
  <div class="media" role="img" aria-label="Client relaxing during a facial treatment" style="background:radial-gradient(ellipse 60px 45px at 62% 62%,#e7cbbb,transparent),linear-gradient(135deg,#ece8e6,#d9d0cb 55%,#f4f2f0)"></div>
  <h3>Lorem ipsum dolor</h3>
  <p>Lorem ipsum dolor sit amet, consectetur adipiscing elit, sed aliqua.</p>
  <a class="btn-details" href="#">View Details</a>
</article>
<article class="product-card" style="left:609px">
  <div class="media" role="img" aria-label="Aesthetic skin care device being prepared" style="background:radial-gradient(ellipse 50px 80px at 85% 40%,#e8927f,transparent),radial-gradient(ellipse 70px 30px at 40% 62%,#8fc4e0,transparent),linear-gradient(135deg,#eef0f2,#d3dae0 60%,#c9ced3)"></div>
  <h3>Lorem ipsum dolor</h3>
  <p>Lorem ipsum dolor sit amet, consectetur adipiscing elit, sed aliqua.</p>
  <a class="btn-details" href="#">View Details</a>
</article>
<article class="product-card" style="left:858px">
  <div class="media" role="img" aria-label="Client enjoying a skin treatment" style="background:radial-gradient(ellipse 50px 55px at 35% 45%,#ead1c2,transparent),radial-gradient(ellipse 60px 60px at 38% 30%,#8d6a58,transparent),linear-gradient(135deg,#eef1f3,#dfe3e6 55%,#f3f2f1)"></div>
  <h3>Lorem ipsum dolor</h3>
  <p>Lorem ipsum dolor sit amet, consectetur adipiscing elit, sed aliqua.</p>
  <a class="btn-details" href="#">View Details</a>
</article>

<section class="about">
  <svg class="abs" style="left:0;top:1440px" width="1200" height="760" viewBox="0 0 1200 760">
    <defs>
      <linearGradient id="waveAbout" x1="0" x2="1">
        <stop offset="0" stop-color="#E54698"/><stop offset="1" stop-color="#F0912C"/>
      </linearGradient>
      <linearGradient id="bandAbout" x1="0" x2="1">
        <stop offset="0" stop-color="#FCEFF6"/><stop offset="1" stop-color="#F9D9EA"/>
      </linearGradient>
    </defs>
    <path d="M0 65 C 120 110, 230 128, 380 115 C 620 90, 850 0, 1000 10 C 1090 16, 1160 45, 1200 60 L1200 700 C 1160 675, 1090 630, 1000 626 C 850 620, 620 720, 380 740 C 230 752, 120 730, 0 685 Z" fill="url(#bandAbout)"/>
    <path d="M0 65 C 120 110, 230 128, 380 115 C 620 90, 850 0, 1000 10 C 1090 16, 1160 45, 1200 60" fill="none" stroke="url(#waveAbout)" stroke-width="8"/>
    <path d="M0 685 C 120 730, 230 752, 380 740 C 620 720, 850 620, 1000 626 C 1090 630, 1160 675, 1200 700" fill="none" stroke="url(#waveAbout)" stroke-width="8"/>
  </svg>
  <div class="about-photo" role="img" aria-label="Portrait of a smiling woman with long dark hair"></div>
  <h2 class="about-title">About Us</h2>
  <p class="about-text">Sed ut perspiciatis unde omnis iste natus error sit voluptatem accu santium doloremque laudantium, totam rem aperiam, eaque ipsa quae ab illo inventore veritatis et quasi architecto beatae vitae dicta sunt explicabo. Nemo enim ipsam voluptatem quia voluptas sit aspernatur aut odit aut fugit, sed quia consequuntur magni dolores eos qui ratione voluptatem sequi nesciunt. Neque porro quisquam est, qui dolorem ipsum quia dolor sit amet, consectetur, adipisci velit, sed quia non magnam aliquam quaerat voluptatem.</p>
  <a class="btn-start" href="#booking">Get Started</a>
</section>

<h2 class="section-title" style="top:2264px">Our Services</h2>

<div class="service-box" style="left:223px">
  <svg width="56" height="70" viewBox="0 0 56 70" fill="none" stroke="#E54698" stroke-width="3">
    <circle cx="28" cy="16" r="13"/>
    <path d="M4 68 V56 C4 44 14 36 28 36 C42 36 52 44 52 56 V68 Z"/>
  </svg>
  <h3>Private Session</h3>
  <p>Lorem ipsum dolor sit amet, consectetur adipiscing</p>
</div>
<div class="service-box" style="left:486px">
  <svg width="96" height="70" viewBox="0 0 96 70" fill="none" stroke="#E54698" stroke-width="3">
    <circle cx="20" cy="22" r="10"/><circle cx="48" cy="16" r="12"/><circle cx="76" cy="22" r="10"/>
    <path d="M2 64 V54 C2 44 10 38 20 38 C27 38 32 41 34 44"/>
    <path d="M94 64 V54 C94 44 86 38 76 38 C69 38 64 41 62 44"/>
    <path d="M24 66 V56 C24 44 34 34 48 34 C62 34 72 44 72 56 V66 Z"/>
  </svg>
  <h3>Group Session</h3>
  <p>Lorem ipsum dolor sit amet, consectetur adipiscing</p>
</div>
<div class="service-box" style="left:749px">
  <svg width="96" height="90" viewBox="0 0 96 90" fill="none" stroke="#E54698" stroke-width="3" style="top:24px">
    <circle cx="48" cy="10" r="8"/><circle cx="30" cy="18" r="7"/><circle cx="66" cy="18" r="7"/>
    <circle cx="18" cy="40" r="9"/><circle cx="78" cy="40" r="9"/><circle cx="48" cy="34" r="11"/>
    <path d="M2 84 V74 C2 64 10 58 18 58 C25 58 30 61 32 64"/>
    <path d="M94 84 V74 C94 64 86 58 78 58 C71 58 66 61 64 64"/>
    <path d="M24 86 V76 C24 62 34 52 48 52 C62 52 72 62 72 76 V86 Z"/>
  </svg>
  <h3>Party</h3>
  <p>Lorem ipsum dolor sit amet, consectetur adipiscing</p>
</div>

<form class="booking" id="booking" action="#">
  <h3>Request an Appointment</h3>
  <input class="field" type="text" placeholder="Full name" style="width:150px">
  <input class="field" type="email" placeholder="Email" style="width:150px">
  <input class="field" type="text" placeholder="Preferred date" style="width:130px">
  <input class="field" type="text" placeholder="Referred by" style="width:150px">
  <button class="btn-send" type="submit">Send Request</button>
</form>

<section class="stories">
  <svg class="abs" style="left:0;top:2700px" width="1200" height="700" viewBox="0 0 1200 700">
    <defs>
      <linearGradient id="waveStories" x1="0" x2="1">
        <stop offset="0" stop-color="#E54698"/><stop offset="1" stop-color="#F0912C"/>
      </linearGradient>
      <linearGradient id="bandStories" x1="0" x2="1">
        <stop offset="0" stop-color="#FBE8D2"/><stop offset="1" stop-color="#FDF5EE"/>
      </linearGradient>
    </defs>
    <path d="M0 66 C 120 110, 230 128, 380 115 C 620 90, 850 0, 1000 10 C 1090 16, 1160 40, 1200 52 L1200 653 C 1160 630, 1090 585, 1000 582 C 850 575, 620 670, 380 688 C 230 698, 120 672, 0 617 Z" fill="url(#bandStories)"/>
    <path d="M0 66 C 120 110, 230 128, 380 115 C 620 90, 850 0, 1000 10 C 1090 16, 1160 40, 1200 52" fill="none" stroke="url(#waveStories)" stroke-width="8"/>
    <path d="M0 617 C 120 672, 230 698, 380 688 C 620 670, 850 575, 1000 582 C 1090 585, 1160 630, 1200 653" fill="none" stroke="url(#waveStories)" stroke-width="8"/>
  </svg>
  <h2 class="section-title" style="top:2870px">Our Stories</h2>
  <div class="story" style="left:111px" role="img" aria-label="Before and after lip treatment comparison">
    <div class="abs" style="inset:0;background:radial-gradient(ellipse 90px 30px at 50% 52%,#d2848c,transparent),radial-gradient(ellipse 200px 160px at 50% 45%,#eccab8,transparent),linear-gradient(90deg,#f7f3f1,#f2e4dc 50%,#f7f3f1)"></div>
    <span class="split"></span>
  </div>
  <div class="story" style="left:617px" role="img" aria-label="Before and after eye area rejuvenation comparison">
    <div class="abs" style="inset:0;background:radial-gradient(ellipse 130px 150px at 55% 45%,#d7ad93,transparent),radial-gradient(ellipse 180px 70px at 55% 8%,#6e4b3a,transparent),linear-gradient(90deg,#f6f5f3,#eee6e0 50%,#f6f5f3)"></div>
    <span class="split"></span>
  </div>
</section>

<footer>
  <div class="footer-brand">
    <div class="brand-mark"></div>
    <div class="brand-name">Lumé Muse</div>
    <div class="brand-sub">CONCIERGE AESTHETICS</div>
  </div>
  <div class="footer-col" style="left:486px">
    <h4>Quick Links</h4>
    <a href="#">Home</a><a href="#">About</a><a href="#">Services</a><a href="#">Products</a><a href="#">Stories</a>
  </div>
  <div class="footer-col" style="left:725px">
    <h4>Service</h4>
    <a href="#">Private Session</a><a href="#">Group Session</a><a href="#">Party</a>
  </div>
  <div class="footer-col" style="left:968px">
    <h4>Conditions</h4>
    <a href="#">Delivery</a><a href="#">Terms of trade</a><a href="#">Privacy policy</a>
  </div>
  <div class="footer-rule"></div>
  <p class="copyright">Copyrights 2022 Lumé Muse &nbsp; | &nbsp; All Rights Reserved</p>
  <div class="social"><span></span><span></span><span></span><span></span></div>
</footer>

</body>
</html>
```